Maris Dovey Studio Business Cards

Hi - using the information and logo provided I require a two sided business card designed with the following information. The business card is a 'mini card' 3.5" x 1.25".

Front of card should be the logo attached but inverted (so the background is the peach colour and the logo white).

Back should have these details. If we can't fit the Pictogrum and Friendwall part can we just put the little logos.

Tessa Varnold

Art and Design Consultant
Dealer - Curator - Events - Styling - Creative Sourcing

P: 0438 217 604
E: tessa@marisdoveystudio.example
W: www.marisdoveystudio.example
I (pictogram image please): marisdoveystudio F (Friendwall image please): MarisDoveyAdviser

Target Market(s)

Galleries, artists, art buyers, interior design clients, event managers, creative types

Industry/Entity Type

Business

```html
<!DOCTYPE html>
<html lang="en">
<head>
<meta charset="utf-8">
<title>Maris Dovey Studio – Mini Business Cards</title>
<link rel="stylesheet" href="https://fonts.googleapis.com/css2?family=Cinzel:wght@400&family=Marcellus&family=Tenor+Sans&display=swap">
<style>
  :root {
    --backdrop: #5e514a;
    --card-dark: #141414;
    --card-mid: #2c2c2c;
    --card-back: #3a3a3a;
    --peach: #f2b59b;
    --peach-soft: #e9a98e;
    --brand-grey: #8f8a86;
    --ink-white: #f4f1ee;
    --rule: rgba(255, 255, 255, 0.14);
  }
  * { box-sizing: border-box; margin: 0; padding: 0; }
  html, body {
    width: 1200px;
    height: 960px;
    overflow: hidden;
    background: var(--backdrop);
  }
  .canvas {
    position: relative;
    width: 1200px;
    height: 960px;
  }
  .card {
    position: absolute;
    width: 870px;
    height: 310px;
    overflow: hidden;
  }
  .card--front {
    left: 34px;
    top: 64px;
    background: radial-gradient(ellipse 55% 75% at 50% 30%, var(--card-mid) 0%, var(--card-dark) 70%);
  }
  .card--back {
    left: 294px;
    top: 474px;
    background: radial-gradient(ellipse 60% 90% at 25% 35%, #474747 0%, var(--card-back) 55%, #2e2e2e 100%);
  }
  .brand-mark {
    position: absolute;
    border-radius: 50%;
    background: var(--peach);
  }
  .card--front .brand-mark { width: 140px; height: 140px; left: 365px; top: 20px; }
  .card--back .brand-mark { width: 128px; height: 128px; left: 120px; top: 26px; }

  .brand-name {
    position: absolute;
    text-align: center;
    font-family: "Cinzel", serif;
    font-weight: 400;
    color: var(--brand-grey);
    line-height: 1;
  }
  .brand-name__main { display: block; letter-spacing: 4px; }
  .brand-name__sub { display: block; letter-spacing: 6px; }
  .card--front .brand-name { left: 0; width: 870px; top: 176px; }
  .card--front .brand-name__main { font-size: 32px; }
  .card--front .brand-name__sub { font-size: 20px; margin-top: 10px; }
  .card--back .brand-name { left: 20px; width: 330px; top: 166px; }
  .card--back .brand-name__main { font-size: 27px; }
  .card--back .brand-name__sub { font-size: 18px; margin-top: 12px; }

  .services {
    position: absolute;
    left: 0;
    top: 256px;
    width: 870px;
    height: 38px;
    border-top: 1px solid var(--rule);
    border-bottom: 1px solid var(--rule);
    text-align: center;
    font-family: "Marcellus", serif;
    font-size: 22px;
    letter-spacing: 2.6px;
    line-height: 36px;
    color: var(--ink-white);
  }

  .contact {
    position: absolute;
    left: 390px;
    top: 28px;
    width: 450px;
    font-family: "Tenor Sans", sans-serif;
    color: var(--ink-white);
  }
  .contact__name {
    font-size: 40px;
    line-height: 1;
    color: var(--peach);
    letter-spacing: 0.5px;
  }
  .contact__title {
    margin-top: 8px;
    font-size: 17px;
  }
  .contact__rule {
    margin-top: 14px;
    height: 1px;
    background: var(--rule);
  }
  .contact__list { margin-top: 10px; list-style: none; }
  .contact__row {
    display: flex;
    height: 30px;
    align-items: center;
    font-size: 19px;
  }
  .contact__label { width: 72px; color: var(--peach-soft); }
  .contact__colon { width: 26px; color: var(--peach-soft); }

  .socials {
    position: absolute;
    left: 44px;
    top: 246px;
    display: flex;
    align-items: center;
    font-family: "Tenor Sans", sans-serif;
    font-size: 22px;
    color: var(--ink-white);
  }
  .social { display: flex; align-items: center; }
  .social__square {
    width: 32px;
    height: 32px;
    background: var(--ink-white);
    border-radius: 3px;
    margin-right: 26px;
  }
  .socials__divider {
    width: 1px;
    height: 26px;
    background: var(--ink-white);
    margin: 0 70px 0 56px;
  }
</style>
</head>
<body>
<main class="canvas">

  <section class="card card--front" aria-label="Card front">
    <div class="brand-mark" aria-hidden="true"></div>
    <p class="brand-name">
      <span class="brand-name__main">MARIS DOVEY</span>
      <span class="brand-name__sub">STUDIO</span>
    </p>
    <p class="services">Dealer | Curator | Events | Styling | Creative Sourcing</p>
  </section>

  <section class="card card--back" aria-label="Card back">
    <div class="brand-mark" aria-hidden="true"></div>
    <p class="brand-name">
      <span class="brand-name__main">MARIS DOVEY</span>
      <span class="brand-name__sub">STUDIO</span>
    </p>

    <div class="contact">
      <h1 class="contact__name">Tessa Varnold</h1>
      <p class="contact__title">Art and Design Consultant</p>
      <div class="contact__rule"></div>
      <ul class="contact__list">
        <li class="contact__row"><span class="contact__label">Phone</span><span class="contact__colon">:</span><span>0438 217 604</span></li>
        <li class="contact__row"><span class="contact__label">Email</span><span class="contact__colon">:</span><span>tessa@marisdoveystudio.example</span></li>
        <li class="contact__row"><span class="contact__label">Web</span><span class="contact__colon">:</span><span>www.marisdoveystudio.example</span></li>
      </ul>
    </div>

    <div class="socials">
      <div class="social"><span class="social__square" aria-hidden="true"></span><span>MarisDoveyAdviser</span></div>
      <span class="socials__divider" aria-hidden="true"></span>
      <div class="social"><span class="social__square" aria-hidden="true"></span><span>marisdoveystudio</span></div>
    </div>
  </section>

</main>
</body>
</html>
```